Im open to ideas.. I was thinking on my business cards aswell as my logo. a place for my name. email. phone number and abn..

ive attched a file with my business logo. which i dont love the colours.. i was think a dark background with charcoal letters so something along those colour schumes but im open to ideas..

BRM Constructions

```html
<!DOCTYPE html>
<html lang="en">
<head>
<meta charset="UTF-8">
<title>BRM Constructions — Business Card</title>
<link rel="stylesheet" href="https://fonts.googleapis.com/css2?family=Questrial&display=swap">
<style>
  :root {
    --page-bg: #e4e4e2;
    --stone-dark: #232323;
    --stone-mid: #363534;
    --stone-light: #454341;
    --ink: #ffffff;
    --rule: rgba(255,255,255,0.75);
  }
  * { margin: 0; padding: 0; box-sizing: border-box; }
  html, body {
    width: 1200px;
    height: 800px;
    overflow: hidden;
    background: var(--page-bg);
    font-family: "Questrial", sans-serif;
  }
  .business-card {
    position: absolute;
    left: 150px;
    top: 140px;
    width: 900px;
    height: 520px;
    border-radius: 30px;
    overflow: hidden;
    color: var(--ink);
  }
  .stone-texture {
    position: absolute;
    inset: 0;
    background:
      radial-gradient(ellipse at 30% 35%, var(--stone-light) 0%, transparent 55%),
      radial-gradient(ellipse at 75% 70%, var(--stone-mid) 0%, transparent 60%),
      linear-gradient(135deg, var(--stone-mid), var(--stone-dark));
  }
  .brand-name {
    position: absolute;
    left: 80px;
    top: 120px;
    line-height: 1;
  }
  .brand-name .brand-main {
    display: block;
    font-size: 96px;
    letter-spacing: 4px;
  }
  .brand-name .brand-sub {
    display: block;
    margin-top: 8px;
    font-size: 19px;
    letter-spacing: 10px;
  }
  .divider {
    position: absolute;
    left: 130px;
    right: 0;
    top: 305px;
    height: 1px;
    background: var(--rule);
  }
  .contact-block {
    position: absolute;
    right: 48px;
    top: 335px;
    text-align: right;
  }
  .contact-name {
    font-size: 31px;
    letter-spacing: 1px;
  }
  .contact-abn {
    font-size: 14px;
    margin-top: 4px;
    letter-spacing: 0.5px;
  }
  .contact-line {
    display: flex;
    justify-content: flex-end;
    align-items: center;
    gap: 10px;
    font-size: 24px;
    letter-spacing: 0.5px;
  }
  .contact-email { margin-top: 16px; }
  .contact-phone { margin-top: 12px; }
  .contact-icon { width: 24px; height: 24px; flex: none; }
</style>
</head>
<body>
  <div class="business-card">
    <div class="stone-texture" role="img" aria-label="Dark charcoal stone texture background"></div>

    <div class="brand-name">
      <span class="brand-main">BRM</span>
      <span class="brand-sub">CONSTRUCTIONS</span>
    </div>

    <div class="divider"></div>

    <div class="contact-block">
      <div class="contact-name">DANE MERCER</div>
      <div class="contact-abn">ABN: 51 608 392 417</div>
      <div class="contact-line contact-email">
        <svg class="contact-icon" viewBox="0 0 24 24" aria-hidden="true">
          <circle cx="12" cy="12" r="12" fill="#fff"/>
          <rect x="6" y="8" width="12" height="8" rx="1" fill="#2b2b2b"/>
          <polyline points="6.5,8.5 12,12.5 17.5,8.5" fill="none" stroke="#fff" stroke-width="1.2"/>
        </svg>
        <span>DANE.MERCER@BRMBUILD.COM</span>
      </div>
      <div class="contact-line contact-phone">
        <svg class="contact-icon" viewBox="0 0 24 24" aria-hidden="true">
          <circle cx="12" cy="12" r="12" fill="#fff"/>
          <path d="M8.6 6.5c.5-.3 1.1-.2 1.4.3l1.1 1.8c.3.5.2 1.1-.3 1.4l-.8.5c.6 1.4 1.6 2.5 3 3.2l.5-.8c.3-.5.9-.6 1.4-.3l1.8 1.1c.5.3.6.9.3 1.4l-.6 1c-.5.8-1.5 1.1-2.4.8-3.1-1.1-5.4-3.5-6.5-6.6-.3-.9 0-1.9.8-2.4z" fill="#2b2b2b"/>
        </svg>
        <span>202-555-0183</span>
      </div>
    </div>
  </div>
</body>
</html>
```